Redesign This Psychology Website

We would like a slight redesign of this successful psychology (relationship counselling) website:

www.TheKelvaleClinic.com.au

We are updating the website, and we'd like a slight refresh of the design and style.

Please keep to very similar colours, and use the same logo. We're looking for around 10 page templates, however the main one is the home page.

Keep in mind, this website already converts quite well, so we want a new, fresh design in keeping with this one. Please don't bother designing something too extremely different.

thanks :)

Target Market(s)

couples who are looking for relationship counselling. Men and women, 25 - 70, across Australia

Industry/Entity Type

Psychology

Number of Pages Required

5+ page

Font styles to use
Sans Serif

Colors
87cfc6
b7a5cd
ec1f27
ffffff
cee9f5

Requirements
Must have
• a similar look to the current design, just looking for a slight refresh.
• Search bar
• Areas for lots of photos
• same logo
• lots of content areas
Nice to have
• great content areas, where we can display a lot of content and our areas.
Should not have
• no colors like orange, etc.
• should not have a totally different feel.

```html
<!DOCTYPE html>
<html lang="en">
<head>
<meta charset="utf-8">
<title>The Kelvale Clinic – Relationship Counselling</title>
<link rel="stylesheet" href="https://fonts.googleapis.com/css2?family=Open+Sans:wght@400;600;700&display=swap">
<style>
:root{
  --teal:#1f8f96;
  --teal-dark:#16707a;
  --teal-light:#87cfc6;
  --sky:#cee9f5;
  --lilac:#b7a5cd;
  --red:#ec1f27;
  --white:#ffffff;
  --ink:#333b40;
  --muted:#6c7478;
  --line:#e1e6e8;
  --paper:#f4f6f7;
  --orange:#ef8a3a;
  --purple:#9a80c2;
  --brown:#8a4a2c;
  --sea:#2aa39a;
}
*{box-sizing:border-box;margin:0;padding:0}
html,body{width:1200px;height:4905px;overflow:hidden}
body{font-family:"Open Sans",Arial,sans-serif;color:var(--ink);background:var(--white);font-size:13px;line-height:1.6}
a{color:var(--teal);text-decoration:none}
.wrap{width:886px;margin:0 auto;position:relative}

/* header */
.site-header{height:130px;background:var(--white)}
.top-links{position:absolute;right:0;top:6px;display:flex;gap:14px;font-size:11px}
.top-links a{color:var(--muted)}
.top-links .sep{color:var(--line)}
.brand{position:absolute;left:0;top:44px;display:flex;align-items:center;gap:10px}
.brand-dot{width:30px;height:30px;border-radius:50%;background:var(--red)}
.brand-name{font-size:26px;font-weight:700;color:var(--teal);line-height:1}
.brand-tag{position:absolute;left:40px;top:36px;font-size:11px;color:var(--muted);white-space:nowrap}
.header-call{position:absolute;right:0;top:44px;display:flex;align-items:center;gap:12px}
.header-call .call{font-size:15px;font-weight:700;color:var(--teal)}
.header-call .call span{color:var(--ink);font-weight:600;font-size:13px;margin-right:6px}
.cart-btn{background:var(--red);color:var(--white);font-size:12px;font-weight:600;padding:6px 14px;border-radius:3px}
.header-search{position:absolute;right:0;top:86px;width:330px;height:30px;border:1px solid var(--line);border-radius:3px;display:flex;align-items:center;padding:0 10px;font-size:11px;color:var(--muted);justify-content:space-between}

/* nav */
.main-nav{height:40px;background:var(--teal-light)}
.main-nav ul{list-style:none;display:flex;height:40px}
.main-nav li{padding:0 22px;line-height:40px;color:var(--white);font-weight:600;font-size:13px}
.main-nav li.active{background:var(--teal-dark)}

/* hero */
.hero{height:395px;background:linear-gradient(100deg,#d7e6d1 0%,#b9d39a 40%,#8fb863 70%,#c8d8b0 100%);position:relative}
.hero-video{position:absolute;left:157px;top:40px;width:250px;height:300px;background:linear-gradient(180deg,#e8eef0,#c9d6da);display:flex;align-items:center;justify-content:center}
.play{width:56px;height:56px;border-radius:50%;border:3px solid var(--white);display:flex;align-items:center;justify-content:center}

/* service cards */
.services{height:375px;margin-top:40px}
.service-grid{display:flex;gap:22px}
.service-card{width:204px;height:340px;border:1px solid var(--line);background:var(--white);box-shadow:0 2px 6px rgba(0,0,0,.08);text-align:center;position:relative}
.service-card h3{color:var(--white);font-size:14px;font-weight:600;padding:12px 8px;height:52px;line-height:1.3;text-align:left}
.service-card .pic{height:130px;margin:0 10px}
.service-card p{font-size:10.5px;color:var(--muted);padding:10px 12px 6px;line-height:1.45}
.service-card .quiz{font-size:11px;color:var(--teal);text-decoration:underline}
.service-card .more{position:absolute;left:50%;bottom:-14px;transform:translateX(-50%);color:var(--white);font-size:11px;font-weight:600;padding:5px 16px;border-radius:3px;white-space:nowrap}
.c-orange h3,.c-orange .more{background:var(--orange)}
.c-purple h3,.c-purple .more{background:var(--purple)}
.c-brown h3,.c-brown .more{background:var(--brown)}
.c-sea h3,.c-sea .more{background:var(--sea)}

/* main */
.main{height:3490px;margin-top:10px}
.main .wrap{display:flex;gap:22px;height:100%}
.content{width:580px;height:100%;overflow:hidden}
.sidebar{width:284px;height:100%;overflow:hidden}
.content h2{font-size:20px;font-weight:600;color:var(--ink);margin:18px 0 8px;line-height:1.3}
.content p{font-size:12px;color:var(--muted);margin-bottom:10px}
.content p a{text-decoration:underline}
.checks{display:grid;grid-template-columns:1fr 1fr;gap:4px 20px;list-style:none;margin:6px 0 12px}
.checks li{display:flex;align-items:center;gap:8px;font-size:12px;color:var(--muted)}
.locations{display:grid;grid-template-columns:1fr 1fr;gap:4px 20px;list-style:none;margin:6px 0 12px}
.locations li{font-size:12px;color:var(--muted);display:flex;gap:8px;align-items:center}
.locations b{color:var(--teal);font-weight:600}
.photo{height:212px;margin:18px 0}
.photo-a{background:linear-gradient(120deg,#e9dccb,#c9b49a 60%,#efe6da)}
.photo-b{background:linear-gradient(120deg,#d9d2c8,#b7a48f 60%,#ece4da)}
.bullets{display:grid;grid-template-columns:1fr 1fr;list-style:none;gap:4px 20px;margin:6px 0 12px}
.bullets li{font-size:12px;color:var(--muted);display:flex;gap:8px;align-items:center}
.author{display:flex;gap:18px;border-top:1px solid var(--line);border-bottom:1px solid var(--line);padding:14px 0;margin:14px 0}
.author .pic{width:150px;height:150px;flex:none;background:linear-gradient(160deg,#c98f6a,#8c5a40)}
.author h4{color:var(--teal);font-size:15px;margin-bottom:2px}
.author .role{font-size:11px;color:var(--muted);margin-bottom:6px}
.blog h2 span{font-size:15px;font-weight:400;color:var(--muted)}
.blog-grid{display:grid;grid-template-columns:repeat(3,1fr);gap:18px 18px;margin-top:10px}
.post{border:1px solid var(--line);height:226px;background:var(--white);overflow:hidden}
.post .pic{height:120px;background:linear-gradient(150deg,#dfe4e6,#aab5ba)}
.post .date{color:var(--teal);font-size:11px;font-weight:600;padding:10px 12px 2px}
.post .title{font-size:12px;color:var(--ink);padding:0 12px;font-weight:600;line-height:1.45;height:36px}
.post .read{font-size:11px;color:var(--teal);padding:6px 12px 0;font-weight:600}
.load-more{text-align:center;margin-top:24px}
.load-more p{font-size:14px;font-weight:600;color:var(--ink);margin-bottom:6px}
.btn-red{display:inline-block;background:var(--red);color:var(--white);font-size:12px;font-weight:600;padding:7px 22px;border-radius:14px}

/* sidebar */
.finder{background:var(--teal);padding:16px;height:236px;color:var(--white)}
.finder h3{font-size:15px;font-weight:600;text-align:center;line-height:1.3;margin-bottom:12px}
.finder .field{background:var(--white);height:30px;margin-bottom:8px;font-size:11px;color:var(--muted);padding:0 10px;display:flex;align-items:center;justify-content:space-between}
.finder .search{background:var(--red);text-align:center;width:110px;margin:6px auto 0;padding:5px 0;font-weight:600;font-size:12px;border-radius:3px}
.promo{height:146px;margin-top:16px;position:relative;color:var(--white);padding:16px;display:flex;flex-direction:column;justify-content:center;align-items:flex-end;text-align:right}
.promo h4{font-size:17px;font-weight:700;line-height:1.25;width:170px;margin-bottom:14px}
.promo .click{position:absolute;right:12px;bottom:10px;font-size:11px;background:var(--teal-dark);padding:3px 10px;font-weight:600}
.promo-sky{background:linear-gradient(90deg,#b5c0c6 0%,#5e7583 100%)}
.promo-green{background:linear-gradient(90deg,#c6d9a8 0%,#4b8e6a 100%)}
.video-box{margin-top:16px;background:var(--teal);height:230px;padding:10px}
.video-box h4{color:var(--white);font-size:13px;text-align:center;margin-bottom:8px}
.video-box .screen{height:180px;background:linear-gradient(160deg,#e4e0d9,#a5988a);display:flex;align-items:center;justify-content:center}
.assess{height:130px;margin-top:16px;background:linear-gradient(120deg,#e6ecdf,#a9c58d);position:relative}
.assess .bar,.team .bar{position:absolute;left:0;right:0;bottom:0;background:var(--teal);color:var(--white);font-size:11px;font-weight:600;padding:5px 10px}
.team{height:120px;margin-top:12px;background:linear-gradient(120deg,#d7dde0,#8f9ea6);position:relative}
.topics{list-style:none;margin-top:14px}
.topics li{display:flex;height:92px;border-bottom:1px solid var(--line);align-items:center;gap:10px}
.topics .pic{width:110px;height:78px;flex:none;background:linear-gradient(150deg,#e1e5e7,#a9b3b8)}
.topics .txt{flex:1;font-size:12px;color:var(--ink)}
.topics .txt b{color:var(--teal);font-weight:600}
.topics .arrow{width:24px;height:78px;flex:none;background:var(--teal);display:flex;align-items:center;justify-content:center}

/* login */
.members{height:140px;background:var(--paper);margin-top:20px}
.members .wrap{display:flex;align-items:center;height:140px;gap:16px;padding:0 40px}
.members h3{font-size:20px;font-weight:400;color:var(--teal);margin-right:12px}
.members .input{width:220px;height:32px;background:var(--white);border:1px solid var(--line);font-size:11px;color:var(--muted);padding:0 10px;display:flex;align-items:center}
.members .send{background:var(--teal);color:var(--white);font-weight:600;font-size:12px;padding:7px 24px;border-radius:3px}

/* footer */
.site-footer{height:245px;background:var(--teal);margin-top:20px;color:var(--white);text-align:center;padding-top:36px}
.site-footer .call{font-size:15px;font-weight:700}
.site-footer .call span{font-weight:400;margin-right:6px}
.foot-links{margin-top:22px;font-size:12px;display:flex;justify-content:center;gap:16px}
.foot-links a{color:var(--white);text-decoration:underline}
.social{display:flex;justify-content:center;gap:10px;margin-top:20px}
.social span{width:26px;height:26px;border-radius:50%;background:var(--white)}
.copy{margin-top:18px;font-size:11px;opacity:.85}
</style>
</head>
<body>

<header class="site-header">
  <div class="wrap" style="height:130px">
    <nav class="top-links">
      <a>Home</a><span class="sep">|</span><a>About</a><span class="sep">|</span><a>Resources</a><span class="sep">|</span><a>Shop</a><span class="sep">|</span><a>Blog</a><span class="sep">|</span><a>Join Our Associate Program</a><span class="sep">|</span><a>Marriage Counselling</a><span class="sep">|</span><a>Relationship Counselling</a>
    </nav>
    <div class="brand">
      <span class="brand-dot"></span>
      <span class="brand-name">The Kelvale Clinic</span>
      <span class="brand-tag">caring support for every couple, every day</span>
    </div>
    <div class="header-call">
      <div class="call"><span>Call Us</span>1300 555 019</div>
      <div class="cart-btn">My Cart 0 ($0.00)</div>
    </div>
    <div class="header-search">
      <span>Relationship Information Topics</span>
      <svg width="13" height="13" viewBox="0 0 14 14"><circle cx="6" cy="6" r="4.5" fill="none" stroke="#6c7478" stroke-width="1.6"/><line x1="9.3" y1="9.3" x2="13" y2="13" stroke="#6c7478" stroke-width="1.6"/></svg>
    </div>
  </div>
</header>

<nav class="main-nav">
  <div class="wrap">
    <ul>
      <li class="active">Counselling Types</li>
      <li>Relationship Counselling Locations</li>
      <li>Sex Therapy Locations</li>
      <li>Quizzes</li>
      <li>F.A.Q.'s</li>
      <li>Contact</li>
    </ul>
  </div>
</nav>

<section class="hero" role="img" aria-label="Photo of a smiling couple in a green meadow, the man carrying the woman on his back">
  <div class="hero-video" role="img" aria-label="Video still of a psychologist speaking to camera">
    <div class="play"><svg width="20" height="22" viewBox="0 0 20 22"><polygon points="3,1 19,11 3,21" fill="#ffffff"/></svg></div>
  </div>
</section>

<section class="services">
  <div class="wrap service-grid">
    <article class="service-card c-orange">
      <h3>Relationship Counselling</h3>
      <div class="pic" role="img" aria-label="Photo of a couple talking with a counsellor" style="background:linear-gradient(150deg,#e9ddd0,#b79c80)"></div>
      <p>Communication issues, Reconnecting from an affair, Loss of intimacy &amp; love, Power battles...</p>
      <span class="quiz">Take our Relationship Quiz</span>
      <span class="more">Read More</span>
    </article>
    <article class="service-card c-purple">
      <h3>Sex Therapy Counselling</h3>
      <div class="pic" role="img" aria-label="Photo of a couple in a quiet moment" style="background:linear-gradient(150deg,#e6e2ea,#a99bb8)"></div>
      <p>Low libido, Erectile difficulties, Premature ejaculation, Differing desires, Porn addiction...</p>
      <span class="quiz">Take our Sex Quiz</span>
      <span class="more">Read More</span>
    </article>
    <article class="service-card c-brown">
      <h3>Anger Management Counselling</h3>
      <div class="pic" role="img" aria-label="Photo of an upset couple arguing" style="background:linear-gradient(150deg,#e3d9d0,#9d7c66)"></div>
      <p>Managing anger calmly, expressing your anger in healthy ways, staying in control...</p>
      <span class="quiz">Take our Anger Test</span>
      <span class="more">Read More</span>
    </article>
    <article class="service-card c-sea">
      <h3>Narcissism Counselling</h3>
      <div class="pic" role="img" aria-label="Photo of a woman looking distressed" style="background:linear-gradient(150deg,#dde7e6,#86a9a5)"></div>
      <p>Managing narcissistic, supressive, entitled, arrogant and lack of empathy traits...</p>
      <span class="quiz">Check your Narcissism Profile</span>
      <span class="more">Read More</span>
    </article>
  </div>
</section>

<main class="main">
  <div class="wrap">
    <div class="content">
      <h2>We Specialise in Relationship &amp; Marriage Counselling</h2>
      <p>At The Kelvale Clinic, we are a group of PSYCHOLOGISTS, Australia wide, who are passionate about relationships and helping you with yours.</p>
      <p>Our vision is to provide the most highly regarded and comprehensive <a>marriage counselling and relationship counselling</a>, and <a>sex therapy</a> in Australia, at reasonable and affordable rates.</p>
      <p>When we are experiencing relationship and marriage problems, there can be a lot of pain and confusion, and it can often be difficult to cope with the other areas of our lives when we are struggling with problems with our partner.</p>
      <p>We are not taught about relationships and how to have a good one in our schools, so most of us are doing the best we know how, but lack the knowledge on how to create a better relationship.</p>

      <h2>Our Kelvale Relationship Psychologists</h2>
      <p>Our team of 70 hand-chosen <a>Registered Psychologists</a> in 81 locations Australia wide, are individually selected for their knowledge, experience, compassion, and evidence-based approach to marriage counselling and sexual therapy.</p>
      <p>In addition all our Psychologists take part in our linked Relationship Counselling Methodologies Training and yearly further conferences, ensuring you are in safe and experienced hands.</p>
      <p><a>As we are Psychologists, you may be eligible for Medicare &amp; Private Health Insurance Rebates.</a> We are highly experienced and can help you with all kinds of relationship difficulties.</p>
      <p>Here are some of the common ones:</p>
      <ul class="checks">
        <li><svg width="12" height="12" viewBox="0 0 12 12"><rect width="12" height="12" fill="#1f8f96"/><polyline points="2.5,6 5,8.5 9.5,3.5" fill="none" stroke="#fff" stroke-width="1.6"/></svg>Affairs</li>
        <li><svg width="12" height="12" viewBox="0 0 12 12"><rect width="12" height="12" fill="#1f8f96"/><polyline points="2.5,6 5,8.5 9.5,3.5" fill="none" stroke="#fff" stroke-width="1.6"/></svg>Problems from childhood</li>
        <li><svg width="12" height="12" viewBox="0 0 12 12"><rect width="12" height="12" fill="#1f8f96"/><polyline points="2.5,6 5,8.5 9.5,3.5" fill="none" stroke="#fff" stroke-width="1.6"/></svg>Controlling behaviour</li>
        <li><svg width="12" height="12" viewBox="0 0 12 12"><rect width="12" height="12" fill="#1f8f96"/><polyline points="2.5,6 5,8.5 9.5,3.5" fill="none" stroke="#fff" stroke-width="1.6"/></svg>Problems with parenting your children</li>
        <li><svg width="12" height="12" viewBox="0 0 12 12"><rect width="12" height="12" fill="#1f8f96"/><polyline points="2.5,6 5,8.5 9.5,3.5" fill="none" stroke="#fff" stroke-width="1.6"/></svg>Verbal abuse</li>
        <li><svg width="12" height="12" viewBox="0 0 12 12"><rect width="12" height="12" fill="#1f8f96"/><polyline points="2.5,6 5,8.5 9.5,3.5" fill="none" stroke="#fff" stroke-width="1.6"/></svg>Step children and in-laws</li>
        <li><svg width="12" height="12" viewBox="0 0 12 12"><rect width="12" height="12" fill="#1f8f96"/><polyline points="2.5,6 5,8.5 9.5,3.5" fill="none" stroke="#fff" stroke-width="1.6"/></svg>Imbalance of power</li>
        <li><svg width="12" height="12" viewBox="0 0 12 12"><rect width="12" height="12" fill="#1f8f96"/><polyline points="2.5,6 5,8.5 9.5,3.5" fill="none" stroke="#fff" stroke-width="1.6"/></svg>All forms of family problems</li>
        <li><svg width="12" height="12" viewBox="0 0 12 12"><rect width="12" height="12" fill="#1f8f96"/><polyline points="2.5,6 5,8.5 9.5,3.5" fill="none" stroke="#fff" stroke-width="1.6"/></svg>Lack of intimacy</li>
        <li><svg width="12" height="12" viewBox="0 0 12 12"><rect width="12" height="12" fill="#1f8f96"/><polyline points="2.5,6 5,8.5 9.5,3.5" fill="none" stroke="#fff" stroke-width="1.6"/></svg>Anger management problems</li>
        <li><svg width="12" height="12" viewBox="0 0 12 12"><rect width="12" height="12" fill="#1f8f96"/><polyline points="2.5,6 5,8.5 9.5,3.5" fill="none" stroke="#fff" stroke-width="1.6"/></svg>Poor communication</li>
        <li><svg width="12" height="12" viewBox="0 0 12 12"><rect width="12" height="12" fill="#1f8f96"/><polyline points="2.5,6 5,8.5 9.5,3.5" fill="none" stroke="#fff" stroke-width="1.6"/></svg>Porn addiction problems</li>
        <li><svg width="12" height="12" viewBox="0 0 12 12"><rect width="12" height="12" fill="#1f8f96"/><polyline points="2.5,6 5,8.5 9.5,3.5" fill="none" stroke="#fff" stroke-width="1.6"/></svg>Loss of love</li>
        <li><svg width="12" height="12" viewBox="0 0 12 12"><rect width="12" height="12" fill="#1f8f96"/><polyline points="2.5,6 5,8.5 9.5,3.5" fill="none" stroke="#fff" stroke-width="1.6"/></svg>Pornography problems</li>
        <li><svg width="12" height="12" viewBox="0 0 12 12"><rect width="12" height="12" fill="#1f8f96"/><polyline points="2.5,6 5,8.5 9.5,3.5" fill="none" stroke="#fff" stroke-width="1.6"/></svg>Relationship neglect</li>
        <li><svg width="12" height="12" viewBox="0 0 12 12"><rect width="12" height="12" fill="#1f8f96"/><polyline points="2.5,6 5,8.5 9.5,3.5" fill="none" stroke="#fff" stroke-width="1.6"/></svg>Affairs</li>
        <li><svg width="12" height="12" viewBox="0 0 12 12"><rect width="12" height="12" fill="#1f8f96"/><polyline points="2.5,6 5,8.5 9.5,3.5" fill="none" stroke="#fff" stroke-width="1.6"/></svg>Sexual problems</li>
      </ul>

      <h2>Our Relationship Counselling Approach</h2>
      <p>It is an important part of our policy to take a <a>very positive approach</a> to our relationship counselling.</p>
      <p>We feel it is important to really understand the problems and perspectives of each of you, and at the same time, we find that most couples are looking to find a positive action plan and way through their problems to make changes which have a positive impact and a real sense of hope for their relationship.</p>
      <p>Read more about our approach to counselling in our <a>relationship counselling services</a>, and <a>frequently asked questions about the relationship and marriage counselling process.</a></p>

      <h2>Our Relationship Counselling Locations across Australia</h2>
      <p>Here are some of the common areas:</p>
      <ul class="locations">
        <li><b>Sydney</b> – 19 centres</li><li><b>Adelaide</b> – 4 centres</li>
        <li><b>Canberra</b> – 2 centres</li><li><b>Gold Coast</b> – 3 centres</li>
        <li><b>Melbourne</b> – 21 centres</li><li><b>Sunshine Coast</b> – 2 centres</li>
        <li><b>Perth</b> – 10 centres</li><li><b>Cairns</b> – 1 centre</li>
        <li><b>Brisbane</b> – 14 centres</li><li><b>Townsville</b> – 1 centre</li>
        <li><b>Wollongong</b> – 2 centres</li><li><b>Hobart</b> – 2 centres</li>
        <li><b>Central Coast</b> – 2 centres</li>
      </ul>
      <p>Contact us to also provide after hours and Saturday sessions for your convenience. Click the <a>Locations</a> tab for more information about one of our caring psychologists in your area.</p>

      <div class="photo photo-a" role="img" aria-label="Photo of a happy couple unpacking moving boxes"></div>

      <h2>Communication is a vital skill but not often taught to us.</h2>
      <p>Most people find that their ways of communicating with each other are what hamper us from having a happy healthy relationship.</p>
      <p>Effective Interpersonal Communication skills are not something that we are usually taught. But for almost everyone who is having difficulties in their relationship, they feel that they are trying to communicate their thoughts and feelings but that their partner is not listening.</p>
      <p>Most people have found that they, themselves don't want to listen when they experience their partner as not wanting to listen to them, so the net effect is that neither person gets listened to, and both are frustrated.</p>
      <p>So learning how to communicate your honest thoughts and feelings in a way that your partner does truly listen is a crucial skill for you to feel that you are in a fulfilling relationship. We can show you some simple but effective principles on how to do this with each other.</p>

      <div class="photo photo-b" role="img" aria-label="Photo of a couple sitting together and talking"></div>

      <h2>We as individuals have specific patterns in our relationships</h2>
      <p>We can also assist you if you want individual help and guidance on your relationship, so you can learn what the patterns in your relationships are showing you about yourself.</p>
      <p>If you have been in a number of relationships and have found yourself repeating the same kind of experiences, which is often the way our relationships play out, we can help you discover the patterns that you might be unwittingly setting up, so you can change these and move into more rewarding relationships in the future.</p>
      <p>Want more information? Please help yourself to our free articles on common relationship problems you may be encountering including:</p>
      <ul class="bullets">
        <li><svg width="12" height="12" viewBox="0 0 12 12"><rect width="12" height="12" fill="#1f8f96"/><polyline points="2.5,6 5,8.5 9.5,3.5" fill="none" stroke="#fff" stroke-width="1.6"/></svg>Why relationships go wrong</li>
        <li><svg width="12" height="12" viewBox="0 0 12 12"><rect width="12" height="12" fill="#1f8f96"/><polyline points="2.5,6 5,8.5 9.5,3.5" fill="none" stroke="#fff" stroke-width="1.6"/></svg>How to recover from an affair</li>
        <li><svg width="12" height="12" viewBox="0 0 12 12"><rect width="12" height="12" fill="#1f8f96"/><polyline points="2.5,6 5,8.5 9.5,3.5" fill="none" stroke="#fff" stroke-width="1.6"/></svg>Have you lost yourself in your relationship</li>
        <li><svg width="12" height="12" viewBox="0 0 12 12"><rect width="12" height="12" fill="#1f8f96"/><polyline points="2.5,6 5,8.5 9.5,3.5" fill="none" stroke="#fff" stroke-width="1.6"/></svg>The secret to more sex</li>
      </ul>
      <p>For <a>the latest short, up-to-date articles on relationships</a>, relationship problems and relationship counselling, please also check out our relationship counselling blog.</p>

      <div class="author">
        <div class="pic" role="img" aria-label="Portrait photo of the psychologist"></div>
        <div>
          <h4>Marla</h4>
          <div class="role">Registered Psychologist Brisbane</div>
          <p>Suite 4, 12 Example Lane, Riverside Park, Northgate QLD 4000</p>
          <p>You can read more about <a>relationship counselling here</a>.</p>
        </div>
      </div>

      <section class="blog">
        <h2>Our Blog <span>( Relationships &amp; Sex )</span></h2>
        <div class="blog-grid">
          <article class="post"><div class="pic" role="img" aria-label="Photo of a thoughtful woman"></div><div class="date">February 24, 2017</div><div class="title">What can I do if I'm living with a Narcissist?</div><div class="read">Read More »</div></article>
          <article class="post"><div class="pic" role="img" aria-label="Photo of a woman looking away"></div><div class="date">February 24, 2017</div><div class="title">Why am I with a Narcissist?</div><div class="read">Read More »</div></article>
          <article class="post"><div class="pic" role="img" aria-label="Photo of a man resting his head on his hand"></div><div class="date">February 24, 2017</div><div class="title">How Do I Know If I'm With a Narcissist?</div><div class="read">Read More »</div></article>
          <article class="post"><div class="pic" role="img" aria-label="Photo of a thoughtful woman"></div><div class="date">February 24, 2017</div><div class="title">What can I do if I'm living with a Narcissist?</div><div class="read">Read More »</div></article>
          <article class="post"><div class="pic" role="img" aria-label="Photo of a woman looking away"></div><div class="date">February 24, 2017</div><div class="title">Why am I with a Narcissist?</div><div class="read">Read More »</div></article>
          <article class="post"><div class="pic" role="img" aria-label="Photo of a man resting his head on his hand"></div><div class="date">February 24, 2017</div><div class="title">How Do I Know If I'm With a Narcissist?</div><div class="read">Read More »</div></article>
          <article class="post"><div class="pic" role="img" aria-label="Photo of a thoughtful woman"></div><div class="date">February 24, 2017</div><div class="title">What can I do if I'm living with a Narcissist?</div><div class="read">Read More »</div></article>
          <article class="post"><div class="pic" role="img" aria-label="Photo of a woman looking away"></div><div class="date">February 24, 2017</div><div class="title">Why am I with a Narcissist?</div><div class="read">Read More »</div></article>
          <article class="post"><div class="pic" role="img" aria-label="Photo of a man resting his head on his hand"></div><div class="date">February 24, 2017</div><div class="title">How Do I Know If I'm With a Narcissist?</div><div class="read">Read More »</div></article>
        </div>
        <div class="load-more">
          <p>Would you like to read more?</p>
          <span class="btn-red">Load More »</span>
        </div>
      </section>
    </div>

    <aside class="sidebar">
      <div class="finder">
        <h3>Find Our Psychologist<br>Near You</h3>
        <div class="field">Type of Counselling <svg width="9" height="6" viewBox="0 0 9 6"><polygon points="0,0 9,0 4.5,6" fill="#6c7478"/></svg></div>
        <div class="field">Location</div>
        <div class="field">Postcode</div>
        <div class="search">Search</div>
      </div>
      <div class="promo promo-sky" role="img" aria-label="Photo of a worried woman with banner text"><h4>Is Anxiety, Depression Or Stress bothering YOU?</h4><span class="click">Click Here »</span></div>
      <div class="promo promo-green" role="img" aria-label="Photo of a health professional with banner text"><h4>Information for Relationship GPs &amp; Health Professionals</h4><span class="click">Click Here »</span></div>
      <div class="video-box">
        <h4>What To Expect From Counselling</h4>
        <div class="screen" role="img" aria-label="Video still of a counselling session"><div class="play"><svg width="20" height="22" viewBox="0 0 20 22"><polygon points="3,1 19,11 3,21" fill="#ffffff"/></svg></div></div>
      </div>
      <div class="assess" role="img" aria-label="Photo of a smiling couple outdoors"><span class="bar">Do Our Relationship Assessment »</span></div>
      <div class="team" role="img" aria-label="Photo of the psychologist team"><span class="bar">Find out more about us »</span></div>
      <ul class="topics">
        <li><div class="pic" role="img" aria-label="Photo of an upset couple"></div><div class="txt">How to deal with an affair?</div><div class="arrow"><svg width="8" height="12" viewBox="0 0 8 12"><polyline points="1,1 6,6 1,11" fill="none" stroke="#fff" stroke-width="2"/></svg></div></li>
        <li><div class="pic" role="img" aria-label="Photo of a couple embracing"></div><div class="txt"><b>Some Sex Relationships &amp; Counselling</b></div><div class="arrow"><svg width="8" height="12" viewBox="0 0 8 12"><polyline points="1,1 6,6 1,11" fill="none" stroke="#fff" stroke-width="2"/></svg></div></li>
        <li><div class="pic" role="img" aria-label="Photo of a woman looking sad"></div><div class="txt">Are you living with a narcissist?</div><div class="arrow"><svg width="8" height="12" viewBox="0 0 8 12"><polyline points="1,1 6,6 1,11" fill="none" stroke="#fff" stroke-width="2"/></svg></div></li>
        <li><div class="pic" role="img" aria-label="Photo of a couple apart in bed"></div><div class="txt">Is one of you an Intimacy Withholder?</div><div class="arrow"><svg width="8" height="12" viewBox="0 0 8 12"><polyline points="1,1 6,6 1,11" fill="none" stroke="#fff" stroke-width="2"/></svg></div></li>
        <li><div class="pic" role="img" aria-label="Photo of a man looking at a screen"></div><div class="txt">Is too much porn affecting your relationship?</div><div class="arrow"><svg width="8" height="12" viewBox="0 0 8 12"><polyline points="1,1 6,6 1,11" fill="none" stroke="#fff" stroke-width="2"/></svg></div></li>
        <li><div class="pic" role="img" aria-label="Photo of a couple in conversation"></div><div class="txt">Is your relationship difficult? Is your partner counselling?</div><div class="arrow"><svg width="8" height="12" viewBox="0 0 8 12"><polyline points="1,1 6,6 1,11" fill="none" stroke="#fff" stroke-width="2"/></svg></div></li>
      </ul>
      <div class="promo promo-sky" role="img" aria-label="Photo of a worried woman with banner text"><h4>Is Anxiety, Depression Or Stress bothering YOU?</h4><span class="click">Click Here »</span></div>
      <div class="promo promo-green" role="img" aria-label="Photo of a health professional with banner text"><h4>Information for Relationship GPs &amp; Health Professionals</h4><span class="click">Click Here »</span></div>
    </aside>
  </div>
</main>

<section class="members">
  <div class="wrap">
    <h3>Members Login</h3>
    <div class="input">Enter Your Details</div>
    <div class="input">Password</div>
    <span class="send">Send</span>
  </div>
</section>

<footer class="site-footer">
  <div class="call"><span>Call Us</span>1300 555 019</div>
  <nav class="foot-links"><a>Privacy Policy</a><span>|</span><a>Terms &amp; Conditions</a><span>|</span><a>Site Map</a><span>|</span><a>Associate Psychologists Program</a><span>|</span><a>Contact Us</a></nav>
  <div class="social"><span></span><span></span><span></span></div>
  <div class="copy">© 2017 The Kelvale Clinic. All Rights Reserved</div>
</footer>

</body>
</html>
```